Wix Design for a Clothing Design Web Marketing Site

We need a Wix design and content (including any images and copy) for a clothing design web storefront, Sew To Suit (or sewtosuit). Rough ideas and content can be found at http://marenvoltis.wix.com/sewtosuit.

Sew To Suit is an innovative business concept that combines fashion and entertainment. The business model allows customers to actively participate in the creation of fashion designs/concepts , visualize the garment in the customer’s body in 3D, and buy the physical garment made specially to fit the customer.
The fashion consultant will be able to create the design based on client's desires and test various possibilities (size, fabric, cut, etc..) in front of the customer, using software Drapova (the software is a key component of this business model)
(when developing the website use images from Drapova)
After the design is created, the customer can choose to order the actual piece. The garment will be made according to the created design, the customer measurements.

Target Market(s)

Primarily women from 25 to 45, who are fashion enthusiasts and appreciate fit and exclusivity. They are hedonistic shoppers, who shop for entertainment.
Men (metrosexuals) who are fashion enthusiasts, also hedonistic shoppers.

Industry/Entity Type

Clothing

Font styles to use
Serif
Sans Serif

Requirements
Must have
• Must have a landing page (home) or section, that gives the consumer an idea of what Sew To Suit will do for them, an about page or section that tells about the company and product, a how it works page or section that describes how it works (http://marenvoltis.wix.com/sewtosuit#!services3/c192y), and page or section about pricing, and a page or section on how to contact us.
Nice to have
• Very modern and clean. The website must be based on the main picture of the studio in the example. If that studio is the store, what will the website look like?
• Colors yellow, grey and white. Use the zig zag in yellow and white. You can change the size of the lines. The zig zagi gives the modern and bold accent. Outfits in pictures must show nicely tailored garments.

```html
<!DOCTYPE html>
<html lang="en">
<head>
<meta charset="utf-8">
<title>Sew To Suit</title>
<link rel="stylesheet" href="https://fonts.googleapis.com/css2?family=Roboto:wght@400;500;700&family=Raleway:wght@500;600&family=Playfair+Display:wght@700&display=swap">
<style>
:root{
  --yellow:#f2e600;
  --yellow-pale:#f7f3a0;
  --grey-dark:#555555;
  --grey-nav:#666666;
  --ink:#222222;
  --muted:#888888;
  --white:#ffffff;
  --accent-red:#e8473c;
}
*{box-sizing:border-box;margin:0;padding:0}
html,body{width:1200px;height:2166px;overflow:hidden}
body{position:relative;background:var(--white);font-family:"Roboto",Arial,sans-serif;color:var(--ink)}
.abs{position:absolute}

/* header */
.header-band{left:0;top:0;width:1200px;height:148px;background:linear-gradient(135deg,#faf6b8,#f4ee7c 50%,#faf6b8)}
.brand{left:112px;top:96px;display:flex;align-items:center;gap:10px;font-family:"Roboto",sans-serif;font-weight:700;font-size:22px;color:var(--ink)}
.brand-mark{width:14px;height:14px;background:var(--ink)}
.account{left:870px;top:12px;font-size:12px;letter-spacing:1px;color:#555;display:flex;align-items:center;gap:6px}
.search{left:622px;top:68px;width:478px;height:34px;display:flex}
.search-field{flex:1;background:var(--white);border:1px solid #ddd;font-size:12px;color:#999;padding:9px 10px}
.search-btn{width:90px;background:var(--yellow);font-size:13px;font-weight:500;text-align:center;line-height:34px}
.recommended{left:620px;top:114px;font-size:12px;color:#444}

/* nav */
.nav{left:0;top:148px;width:1200px;height:45px;background:var(--grey-nav);display:flex;align-items:center}
.nav-list{position:absolute;left:100px;top:0;height:45px;display:flex;list-style:none}
.nav-list li{color:var(--white);font-size:14px;line-height:45px;padding:0 24px;border-right:1px solid #888;letter-spacing:.3px}
.nav-list li:first-child{padding:0 6px 0 20px;border-right:none;position:relative;margin-right:30px}
.nav-list li:first-child::after{content:"";position:absolute;left:0;right:0;bottom:6px;height:2px;background:var(--yellow)}
.nav-list li:last-child{border-right:none}
.social{position:absolute;left:920px;top:15px;display:flex;gap:9px}
.social span{width:14px;height:14px;border-radius:50%;background:var(--white)}

/* hero */
.hero{left:100px;top:208px;width:1000px;height:427px;background:linear-gradient(120deg,#e8c98f 0%,#d9a867 35%,#c98e55 60%,#e6c785 100%)}
.hero-title{left:498px;top:311px;width:572px;height:55px;background:var(--yellow);font-family:"Raleway",sans-serif;font-weight:600;font-size:37px;letter-spacing:1.5px;line-height:55px;text-align:center;color:var(--ink)}
.hero-sub{left:765px;top:384px;font-family:"Raleway",sans-serif;font-size:16px;letter-spacing:.5px;color:var(--ink)}

/* promo */
.promo{left:126px;top:667px;width:938px;height:295px;border:1px dashed #888}
.promo-photo{top:3px;height:287px}
.promo-photo.p1{left:3px;width:173px;background:linear-gradient(#8a9a6a,#a89b78)}
.promo-photo.p2{left:177px;width:173px;background:linear-gradient(#f2f0ec,#d8d4cc)}
.promo-photo.p3{left:352px;width:173px;background:linear-gradient(#d7dbd6,#8a3a34)}
.promo-offer{left:527px;top:3px;width:408px;height:287px;background:#0d0d0d;text-align:center;color:var(--white)}
.offer-head{position:absolute;left:0;right:0;top:22px;font-family:"Playfair Display",serif;font-weight:700;font-size:44px;color:var(--yellow);letter-spacing:1px}
.offer-sub{position:absolute;left:0;right:0;top:80px;font-family:"Playfair Display",serif;font-size:28px;letter-spacing:3px}
.offer-num{position:absolute;left:110px;top:110px;font-family:"Roboto",sans-serif;font-size:138px;line-height:150px}
.offer-pct{position:absolute;left:272px;top:148px;font-size:32px}
.offer-off{position:absolute;left:268px;top:186px;font-size:12px}

/* products */
.card{width:279px;height:285px;border:1px solid #ddd;background:var(--white)}
.card-photo{position:absolute;left:6px;top:6px;width:265px;height:221px}
.card-bar{position:absolute;left:-1px;right:-1px;bottom:-1px;height:50px;background:var(--grey-dark);display:flex;align-items:center;padding:0 8px 0 18px;color:var(--white);font-size:17px}
.price-old{text-decoration:line-through;color:#ccc;margin-right:12px}
.price-new{flex:1}
.add-cart{background:var(--yellow);color:var(--ink);font-size:14px;height:32px;line-height:32px;padding:0 10px;display:flex;align-items:center;gap:6px}

/* footer */
.footer-band{left:0;top:1680px;width:1200px;height:486px;background:linear-gradient(135deg,#faf6b8,#f4ee7c 50%,#faf6b8)}
.footer-box{left:100px;top:1699px;width:1000px;height:381px;background:var(--white);border:2px solid var(--ink)}
.col-title{font-size:20px;font-weight:500;color:var(--ink)}
.fb-title{left:20px;top:50px}
.fb-widget{left:20px;top:91px;width:335px;height:254px;border:1px solid #bbb}
.fb-logo{position:absolute;left:12px;top:14px;width:32px;height:40px;background:#8cc63f;border-radius:4px}
.fb-name{position:absolute;left:58px;top:14px;font-size:13px;font-weight:700;color:#3b5998}
.fb-like{position:absolute;left:58px;top:34px;width:46px;height:16px;background:#4a66a0;color:#fff;font-size:11px;text-align:center;line-height:16px}
.fb-count{position:absolute;left:10px;top:76px;font-size:10px;color:#333}
.fb-count b{font-weight:400;color:#3b5998}
.fb-faces{position:absolute;left:10px;top:98px;display:grid;grid-template-columns:repeat(5,50px);gap:4px}
.fb-faces span{height:50px;background:linear-gradient(#b7a899,#6f6a66)}
.fb-plugin{position:absolute;left:10px;bottom:10px;font-size:9px;color:#666;border-top:1px solid #ddd;width:312px;padding-top:6px}
.divider{top:12px;width:1px;height:356px;background:#ddd}
.feature{left:400px;width:345px;height:90px}
.feature-icon{position:absolute;left:0;top:0;width:54px;height:54px;border-radius:50%;border:1px solid #e2e2e2;display:flex;align-items:center;justify-content:center}
.feature-title{position:absolute;left:68px;top:2px;font-size:19px;font-weight:500}
.feature-text{position:absolute;left:68px;top:32px;width:280px;font-size:12px;line-height:18px;color:var(--muted)}
.links-title{left:792px;top:50px}
.links{left:792px;top:88px;list-style:none;font-size:13px;color:var(--muted)}
.links li{height:31px;position:relative;padding-left:16px;white-space:nowrap;width:195px;overflow:hidden}
.links li::before{content:"";position:absolute;left:0;top:7px;width:5px;height:5px;border-radius:50%;background:#999}
.bottom-links{left:104px;top:2100px;font-size:13px;color:var(--ink);display:flex;gap:12px}
.copyright{left:104px;top:2125px;font-size:12px;color:var(--ink)}
.pay{left:905px;top:2090px;width:185px;height:64px;background:var(--white);border:2px solid #bbb;text-align:center}
.pay-name{font-size:22px;font-weight:700;color:#1d4f91;line-height:28px}
.pay-cards{display:flex;gap:4px;justify-content:center}
.pay-cards span{width:38px;height:20px;background:#d9d9d9;border:1px solid #999}
.pay-cards .bank{font-size:9px;line-height:18px;background:var(--white);color:#333}
</style>
</head>
<body>

<div class="abs header-band" role="img" aria-label="Yellow and white chevron background"></div>
<div class="abs brand"><span class="brand-mark"></span>Sew To Suit</div>
<div class="abs account">
  <svg width="14" height="14" viewBox="0 0 14 14" fill="none" stroke="#555" stroke-width="1.2"><circle cx="7" cy="4.5" r="3"/><path d="M1.5 13c.5-3 2.8-4.5 5.5-4.5s5 1.5 5.5 4.5"/></svg>
  WELCOME , LOGIN / REGISTER
</div>
<div class="abs search"><div class="search-field">Search Keyword...</div><div class="search-btn">SEARCH</div></div>
<div class="abs recommended">Top Recommended: sunscreen mask moisturizing whitening cream cleanser</div>

<nav class="abs nav">
  <ul class="nav-list">
    <li>HOME</li><li>WHAT IS SEW TO SUIT?</li><li>HOW IT WORKS</li><li>PRICE</li><li>CONTACT US</li>
  </ul>
  <div class="social"><span></span><span></span><span></span><span></span><span></span><span></span></div>
</nav>

<div class="abs hero" role="img" aria-label="Woman in denim shorts and plaid shirt sitting beside a sunlit dirt road"></div>
<div class="abs hero-title">CLOTHES MADE SPECIALLY</div>
<div class="abs hero-sub">FOR YOU AND DESIGNED BY YOU!</div>

<section class="abs promo">
  <div class="abs promo-photo p1" role="img" aria-label="Model in olive tunic dress and scarf outdoors"></div>
  <div class="abs promo-photo p2" role="img" aria-label="Model in fitted black off-shoulder dress"></div>
  <div class="abs promo-photo p3" role="img" aria-label="Model in white top with red patterned scarf"></div>
  <div class="abs promo-offer">
    <div class="offer-head">ALL WESTERN</div>
    <div class="offer-sub">SLEEK &amp; SEXY</div>
    <div class="offer-num">30</div>
    <div class="offer-pct">%</div>
    <div class="offer-off">*OFF</div>
  </div>
</section>

<div class="abs card" style="left:126px;top:1010px"><div class="card-photo" role="img" aria-label="Pink polo shirt on model" style="background:linear-gradient(#dfe7ec,#e25a7c)"></div><div class="card-bar"><span class="price-old">$ 45.0</span><span class="price-new">$ 50.0</span><span class="add-cart"><svg width="16" height="14" viewBox="0 0 16 14" fill="none" stroke="#222" stroke-width="1.5"><path d="M1 1h2.5l2 8h8l1.5-5.5H4.5"/><circle cx="6.5" cy="12" r="1"/><circle cx="12.5" cy="12" r="1"/></svg>Add to Cart</span></div></div>
<div class="abs card" style="left:456px;top:1010px"><div class="card-photo" role="img" aria-label="Black vest over red top on model" style="background:linear-gradient(#e8e8e8,#3a2c2c)"></div><div class="card-bar"><span class="price-old">$ 45.0</span><span class="price-new">$ 50.0</span><span class="add-cart"><svg width="16" height="14" viewBox="0 0 16 14" fill="none" stroke="#222" stroke-width="1.5"><path d="M1 1h2.5l2 8h8l1.5-5.5H4.5"/><circle cx="6.5" cy="12" r="1"/><circle cx="12.5" cy="12" r="1"/></svg>Add to Cart</span></div></div>
<div class="abs card" style="left:784px;top:1010px"><div class="card-photo" role="img" aria-label="Black jacket and trousers outfit with handbag" style="background:linear-gradient(#ececec,#4a4444)"></div><div class="card-bar"><span class="price-old">$ 45.0</span><span class="price-new">$ 50.0</span><span class="add-cart"><svg width="16" height="14" viewBox="0 0 16 14" fill="none" stroke="#222" stroke-width="1.5"><path d="M1 1h2.5l2 8h8l1.5-5.5H4.5"/><circle cx="6.5" cy="12" r="1"/><circle cx="12.5" cy="12" r="1"/></svg>Add to Cart</span></div></div>

<div class="abs card" style="left:126px;top:1340px"><div class="card-photo" role="img" aria-label="Model in patterned ethnic jacket" style="background:linear-gradient(#7a6a58,#c9a99a)"></div><div class="card-bar"><span class="price-old">$ 45.0</span><span class="price-new">$ 50.0</span><span class="add-cart"><svg width="16" height="14" viewBox="0 0 16 14" fill="none" stroke="#222" stroke-width="1.5"><path d="M1 1h2.5l2 8h8l1.5-5.5H4.5"/><circle cx="6.5" cy="12" r="1"/><circle cx="12.5" cy="12" r="1"/></svg>Add to Cart</span></div></div>
<div class="abs card" style="left:456px;top:1340px"><div class="card-photo" role="img" aria-label="Model with headscarf and sunglasses against red backdrop" style="background:linear-gradient(135deg,#d83a2e,#2a2a2a)"></div><div class="card-bar"><span class="price-old">$ 45.0</span><span class="price-new">$ 50.0</span><span class="add-cart"><svg width="16" height="14" viewBox="0 0 16 14" fill="none" stroke="#222" stroke-width="1.5"><path d="M1 1h2.5l2 8h8l1.5-5.5H4.5"/><circle cx="6.5" cy="12" r="1"/><circle cx="12.5" cy="12" r="1"/></svg>Add to Cart</span></div></div>
<div class="abs card" style="left:784px;top:1340px"><div class="card-photo" role="img" aria-label="Model in red cloche hat and red velvet top" style="background:linear-gradient(#c8302a,#6a2424)"></div><div class="card-bar"><span class="price-old">$ 45.0</span><span class="price-new">$ 50.0</span><span class="add-cart"><svg width="16" height="14" viewBox="0 0 16 14" fill="none" stroke="#222" stroke-width="1.5"><path d="M1 1h2.5l2 8h8l1.5-5.5H4.5"/><circle cx="6.5" cy="12" r="1"/><circle cx="12.5" cy="12" r="1"/></svg>Add to Cart</span></div></div>

<div class="abs footer-band" role="img" aria-label="Yellow and white chevron background"></div>
<footer class="abs footer-box">
  <h3 class="abs col-title fb-title">Follow us on Friendsphere</h3>
  <div class="abs fb-widget">
    <div class="fb-logo"></div>
    <div class="fb-name">ShopNest</div>
    <div class="fb-like">Like</div>
    <div class="fb-count">45,265 people like <b>ShopNest</b>.</div>
    <div class="fb-faces" role="img" aria-label="Profile photos of followers"><span></span><span></span><span></span><span></span><span></span><span></span><span></span><span></span><span></span><span></span></div>
    <div class="fb-plugin">Friendsphere social plugin</div>
  </div>
  <div class="abs divider" style="left:383px"></div>

  <div class="abs feature" style="top:52px">
    <div class="feature-icon"><svg width="26" height="18" viewBox="0 0 26 18" fill="var(--accent-red)"><rect x="0" y="2" width="15" height="11"/><path d="M16 5h5l4 4v4h-9z"/><circle cx="5" cy="15" r="2.5"/><circle cx="20" cy="15" r="2.5"/></svg></div>
    <div class="feature-title">Free shipping</div>
    <div class="feature-text">Suspendisse ultricies est mi blandit, euismod vestibulum purus.</div>
  </div>
  <div class="abs feature" style="top:155px">
    <div class="feature-icon"><svg width="22" height="22" viewBox="0 0 24 24" fill="var(--accent-red)"><path d="M6.6 10.8a15.1 15.1 0 0 0 6.6 6.6l2.2-2.2c.3-.3.7-.4 1-.2 1.1.4 2.3.6 3.6.6.6 0 1 .4 1 1V20c0 .6-.4 1-1 1A17 17 0 0 1 3 4c0-.6.4-1 1-1h3.5c.6 0 1 .4 1 1 0 1.3.2 2.5.6 3.6.1.3 0 .7-.2 1z"/></svg></div>
    <div class="feature-title">Call us: (800)555-0147</div>
    <div class="feature-text">Praesent ac risus orci. Pellentesque quis quam augue.</div>
  </div>
  <div class="abs feature" style="top:258px">
    <div class="feature-icon"><svg width="24" height="18" viewBox="0 0 24 18" fill="none" stroke="var(--accent-red)" stroke-width="2"><rect x="1" y="1" width="22" height="16" rx="2"/><path d="M1 6h22M5 12h6"/></svg></div>
    <div class="feature-title">Gift cards</div>
    <div class="feature-text">Nunc et molestie metus. Duis cond vel lectus non tincidunt.</div>
  </div>
  <div class="abs divider" style="left:764px"></div>

  <h3 class="abs col-title links-title">Useful Links</h3>
  <ul class="abs links">
    <li>Vestibulum id elementum</li><li>Curabitur cursus vel eros</li><li>Suspendisse dapibus ullam</li><li>Eleifend pharetra</li><li>Donec ultrices quam nec</li><li>Etiam ornare nisi non interdum</li><li>Phasellus eget ultrices dolor</li><li>Ut viverra urna eu</li>
  </ul>
</footer>

<div class="abs bottom-links"><span>Home</span><span>|</span><span>Shop</span><span>|</span><span>Blog</span><span>|</span><span>About</span><span>|</span><span>Collection</span><span>|</span><span>Contact us</span></div>
<div class="abs copyright">© 2015 Copyright Sew To Suit. All Rights Reserved.</div>
<div class="abs pay">
  <div class="pay-name">PayWell</div>
  <div class="pay-cards"><span></span><span></span><span></span><span class="bank">BANK</span></div>
</div>

</body>
</html>
```